New Innovative Counselling and psychotherapy Service needs Business Card design

Keep it simple and professional. On one side, just company name and logo (perhaps in all blue) and maybe a tag line.

On other side (all white) my name and Qualifications in centre

Industry/Entity Type

Health And Wellness

Contact Information for Business Card

Dara Whelby
Counsellor & Psychotherapist
BSc (Psychol.), BA, Dip. (Couns. & Psych.), PG.Cert (CBT), FGTrK, ONRE

I will also require Mobile no, Email and web site address of which I'll pass on to final designer.

Font styles to use
Sans Serif

Requirements
Must have
• My Logo Only and please use the colours in logo that is in it.
Should not have
• Any other images

```html
<!DOCTYPE html>
<html lang="en">
<head>
<meta charset="utf-8">
<title>Thrive Lane — Business Card</title>
<link rel="stylesheet" href="https://fonts.googleapis.com/css2?family=Montserrat:wght@300&family=Open+Sans:wght@400;600&family=Cormorant+Garamond:ital,wght@1,500&display=swap">
<style>
  :root {
    --backdrop: #2b2b2d;
    --card: #1d1e20;
    --card-back: #1a1b1d;
    --pattern: #232427;
    --ink: #f2f2f2;
    --ink-soft: #c9c9cb;
    --rule: #5a5b5e;
    --blue: #3fb2ee;
    --green: #8cc84b;
  }
  * { margin: 0; padding: 0; box-sizing: border-box; }
  html, body {
    width: 1200px; height: 1108px; overflow: hidden;
    background: var(--backdrop);
  }
  .stage {
    position: relative; width: 1200px; height: 1108px;
    display: flex; justify-content: center; align-items: center; gap: 60px;
  }
  .card {
    position: relative; width: 440px; height: 700px;
    border-radius: 22px; overflow: hidden;
    box-shadow: 0 18px 40px rgba(0,0,0,.45);
  }
  .card--front {
    background: var(--card);
    display: flex; flex-direction: column; align-items: center;
    font-family: "Open Sans", sans-serif; color: var(--ink); text-align: center;
  }
  .brand {
    margin-top: 150px;
    display: flex; flex-direction: column; align-items: center; gap: 26px;
  }
  .brand__dot {
    width: 96px; height: 96px; border-radius: 50%; background: var(--blue);
  }
  .brand__name {
    font-family: "Montserrat", sans-serif; font-weight: 300;
    font-size: 46px; letter-spacing: .5px; color: var(--ink-soft);
  }
  .person { margin-top: 48px; }
  .person__name {
    font-size: 26px; font-weight: 600; letter-spacing: .5px; margin-bottom: 4px;
  }
  .person__first { color: var(--blue); }
  .person__last { color: var(--green); }
  .person__role, .person__quals { font-size: 17px; line-height: 1.4; }
  .divider {
    margin-top: 26px; width: 300px;
    display: flex; align-items: center; gap: 8px;
  }
  .divider__line { flex: 1; height: 1px; background: var(--rule); }
  .divider__icon {
    width: 26px; height: 26px; border-radius: 50%; background: var(--blue);
    display: flex; align-items: center; justify-content: center;
  }
  .contact { margin-top: 16px; font-size: 17px; line-height: 1.55; }

  .card--back { background: var(--card-back); }
  .card__pattern {
    position: absolute; inset: 0 0 150px 0; background: var(--pattern);
  }
  .tagline {
    position: absolute; left: 0; right: 0; bottom: 70px;
    font-family: "Cormorant Garamond", serif; font-style: italic; font-weight: 500;
    font-size: 28px; line-height: 1.3; color: var(--ink-soft); text-align: center;
  }
</style>
</head>
<body>
<main class="stage">
  <section class="card card--front">
    <div class="brand">
      <span class="brand__dot"></span>
      <span class="brand__name">Thrive Lane</span>
    </div>
    <div class="person">
      <p class="person__name"><span class="person__first">DARA</span> <span class="person__last">WHELBY</span></p>
      <p class="person__role">Counsellor &amp; Psychotherapist</p>
      <p class="person__quals">BSc (Psychol.), BA, Dip. (Couns. &amp; Psych.),<br>PG.Cert (CBT), FGTrK, ONRE</p>
    </div>
    <div class="divider">
      <span class="divider__line"></span>
      <span class="divider__icon">
        <svg width="14" height="14" viewBox="0 0 24 24" aria-hidden="true"><path fill="#1d1e20" d="M6.6 10.8a15 15 0 0 0 6.6 6.6l2.2-2.2a1 1 0 0 1 1-.25 11.4 11.4 0 0 0 3.6.6 1 1 0 0 1 1 1V20a1 1 0 0 1-1 1A17 17 0 0 1 3 4a1 1 0 0 1 1-1h3.5a1 1 0 0 1 1 1c0 1.25.2 2.45.6 3.6a1 1 0 0 1-.25 1z"/></svg>
      </span>
      <span class="divider__icon">
        <svg width="14" height="14" viewBox="0 0 24 24" aria-hidden="true"><rect x="3" y="5" width="18" height="14" rx="1.5" fill="#1d1e20"/><path d="M3.5 6l8.5 7 8.5-7" stroke="#3fb2ee" stroke-width="1.6" fill="none"/></svg>
      </span>
      <span class="divider__icon">
        <svg width="14" height="14" viewBox="0 0 24 24" aria-hidden="true"><circle cx="12" cy="12" r="9" fill="none" stroke="#1d1e20" stroke-width="2.2"/><path d="M3 12h18M12 3c3 3 3 15 0 18M12 3c-3 3-3 15 0 18" stroke="#1d1e20" stroke-width="1.6" fill="none"/></svg>
      </span>
      <span class="divider__line"></span>
    </div>
    <div class="contact">
      <p>086 5290 417</p>
      <p>info@thrivelane.com</p>
      <p>www.thrivelane.com</p>
    </div>
  </section>

  <section class="card card--back">
    <div class="card__pattern" role="img" aria-label="Tone-on-tone repeating pattern of the company symbol"></div>
    <p class="tagline">Caring For Your Psychological<br>Well-Being Is Our Top Priority</p>
  </section>
</main>
</body>
</html>
```